Stylish new business card needed!

Hello everyone! I am in need of a new business card design for an alarm company here in Hurricane WV. I have all fonts, color codes and logos provided for you use! We are a young company and like the style of a clean sleek looking business card. Would like it double sided, one side holding the logo and the other with your design!
Target Market(s)
The people that are looking for the newest tech for home automation and security
Industry/Entity Type
Alarm services; Home automation
Contact Information for Business Card
Name of person; position (Sales; Installer); Phone Number (555.418.7260); Employee cell Number; Website (www.GuardedByVelk.example); Employee Email; Double sided
Look and feel
Each slider illustrates characteristics of the customer's brand and the style your logo design should communicate.

```html
<!DOCTYPE html>
<html lang="en">
<head>
<meta charset="utf-8">
<title>Guarded By Velk – Business Card</title>
<link rel="stylesheet" href="https://fonts.googleapis.com/css2?family=Arimo:wght@400;700&display=swap">
<style>
  :root {
    --page-bg: #242424;
    --card-bg: #1f1f23;
    --accent: #f58d4c;
    --grey: #9a9a9a;
    --white: #ffffff;
  }
  * { box-sizing: border-box; margin: 0; padding: 0; }
  html, body {
    width: 1200px; height: 780px; overflow: hidden;
    background: var(--page-bg);
    font-family: "Arimo", Arial, sans-serif;
  }
  .canvas {
    width: 1200px; height: 780px;
    display: flex; align-items: center; justify-content: center; gap: 40px;
  }
  .card {
    position: relative;
    width: 540px; height: 309px;
    background: var(--card-bg);
    border-bottom: 5px solid var(--accent);
    box-shadow: 0 14px 30px rgba(0,0,0,.55);
  }
  /* Front side */
  .card-front {
    display: flex; flex-direction: column; align-items: center; justify-content: center;
  }
  .brand-name {
    color: var(--grey);
    font-weight: 700;
    text-align: center;
    line-height: 1;
  }
  .brand-name .brand-prefix { display: block; font-size: 30px; letter-spacing: 2px; margin-bottom: 8px; }
  .brand-name .brand-main { display: block; font-size: 96px; letter-spacing: 10px; }
  .brand-tagline {
    margin-top: 16px;
    color: var(--accent);
    font-weight: 700;
    font-size: 13px;
    letter-spacing: 1.5px;
  }
  /* Back side */
  .card-back {
    display: flex; align-items: center;
    padding: 0 34px 0 56px;
  }
  .person { width: 200px; }
  .person-name { font-size: 27px; font-weight: 700; white-space: nowrap; }
  .person-first { color: var(--accent); }
  .person-last { color: var(--grey); }
  .person-role { color: var(--white); font-size: 15px; font-weight: 700; margin-top: 4px; text-align: right; }
  .divider {
    width: 2px; height: 96px; background: var(--white);
    margin: 0 24px 0 22px;
  }
  .contact-list { list-style: none; }
  .contact-item {
    display: flex; align-items: center; gap: 9px;
    color: var(--white); font-size: 13.5px; line-height: 1;
    margin: 6px 0;
  }
  .contact-icon { width: 14px; height: 14px; flex: none; }
</style>
</head>
<body>
<main class="canvas">
  <section class="card card-front" aria-label="Card front">
    <h1 class="brand-name">
      <span class="brand-prefix">GUARDED BY</span>
      <span class="brand-main">VELK</span>
    </h1>
    <p class="brand-tagline">AUTOMATION AND SECURITY SERVICES</p>
  </section>

  <section class="card card-back" aria-label="Card back">
    <div class="person">
      <p class="person-name"><span class="person-first">Mira</span> <span class="person-last">Halden</span></p>
      <p class="person-role">Sales; Installer</p>
    </div>
    <div class="divider"></div>
    <ul class="contact-list">
      <li class="contact-item">
        <svg class="contact-icon" viewBox="0 0 24 24" aria-hidden="true"><path fill="#f58d4c" d="M6.6 10.8a15 15 0 0 0 6.6 6.6l2.2-2.2a1 1 0 0 1 1-.25 11.4 11.4 0 0 0 3.6.57 1 1 0 0 1 1 1V20a1 1 0 0 1-1 1A17 17 0 0 1 3 4a1 1 0 0 1 1-1h3.5a1 1 0 0 1 1 1c0 1.25.2 2.45.57 3.57a1 1 0 0 1-.25 1z"/></svg>
        555.418.7260
      </li>
      <li class="contact-item">
        <svg class="contact-icon" viewBox="0 0 24 24" aria-hidden="true"><rect x="6" y="2" width="12" height="20" rx="2" fill="none" stroke="#f58d4c" stroke-width="2"/><circle cx="12" cy="18" r="1.2" fill="#f58d4c"/></svg>
        555.902.3314
      </li>
      <li class="contact-item">
        <svg class="contact-icon" viewBox="0 0 24 24" aria-hidden="true"><circle cx="12" cy="12" r="9" fill="none" stroke="#f58d4c" stroke-width="2"/><path d="M3 12h18M12 3c3 3.2 3 14.8 0 18M12 3c-3 3.2-3 14.8 0 18" fill="none" stroke="#f58d4c" stroke-width="1.6"/></svg>
        www.GuardedByVelk.example
      </li>
      <li class="contact-item">
        <svg class="contact-icon" viewBox="0 0 24 24" aria-hidden="true"><rect x="2" y="5" width="20" height="14" rx="1.5" fill="#f58d4c"/><path d="M3 6l9 7 9-7" fill="none" stroke="#1f1f23" stroke-width="1.8"/></svg>
        info@GuardedByVelk.example
      </li>
    </ul>
  </section>
</main>
</body>
</html>
```